Business Card Design

We need a business card design for a Dry cleaners in Brisbane, Australia. We are trying to promote a fresh/clean image consistent with our website. www.pinnelgarmentcare.com.au

Looking for a professional neat card that's easy to read.

Target Market(s)

Customers looking for a professional, fresh and clean drycleaners.

Industry/Entity Type

Business

Contact Information for Business Card

See our existing business card. The Fax number (07) 3468 5270 to be removed.

Requirements
Must have
• All the details on current business card less the fax number.
Nice to have
• I like white text on coloured background. Blue works well as we are located near the water...

```html
<!DOCTYPE html>
<html lang="en">
<head>
<meta charset="utf-8">
<title>Pinnel Garment Care – Business Card</title>
<link href="https://fonts.googleapis.com/css2?family=Source+Sans+3:wght@400;600;700&display=swap" rel="stylesheet">
<style>
  :root {
    --brand-blue: #2b45a8;
    --brand-blue-dark: #1f3488;
    --brand-orange: #e4572a;
    --card-white: #f7f7f8;
    --text-grey: #4a5576;
    --page-bg: #e9e6e1;
  }
  * { margin: 0; padding: 0; box-sizing: border-box; }
  html, body {
    width: 1200px; height: 600px; overflow: hidden;
    background: var(--page-bg);
    font-family: "Source Sans 3", "Myriad Pro", Arial, sans-serif;
  }
  .stage {
    width: 1200px; height: 600px;
    display: flex; align-items: center; justify-content: center; gap: 50px;
  }
  .card {
    position: relative;
    width: 525px; height: 300px;
    background: var(--card-white);
    border-radius: 14px;
    overflow: hidden;
    box-shadow: 0 6px 18px rgba(0,0,0,.18);
  }
  .card-swoosh { position: absolute; inset: 0; width: 100%; height: 100%; }

  /* front */
  .brand {
    position: absolute; left: 34px; top: 38px;
    display: flex; align-items: center; gap: 10px;
  }
  .brand-dot {
    width: 22px; height: 22px; border-radius: 50%;
    background: var(--brand-blue);
  }
  .brand-name {
    font-size: 27px; font-weight: 700; color: var(--brand-blue);
    letter-spacing: -.2px;
  }
  .contact { position: absolute; left: 34px; top: 120px; color: var(--text-grey); }
  .person-name {
    font-size: 21px; font-weight: 600; color: var(--brand-orange);
    margin-bottom: 6px;
  }
  .address { font-size: 13.5px; line-height: 17px; margin-bottom: 8px; }
  .contact-list { list-style: none; font-size: 13.5px; line-height: 18px; }
  .contact-list li { display: flex; align-items: center; gap: 8px; }
  .contact-icon { width: 11px; height: 11px; flex: none; }

  /* back */
  .locations {
    position: absolute; right: 26px; bottom: 22px;
    color: #fff; font-size: 14px; letter-spacing: .3px;
  }
</style>
</head>
<body>
<main class="stage">

  <section class="card card-front" aria-label="Business card front">
    <svg class="card-swoosh" viewBox="0 0 525 300" preserveAspectRatio="none" aria-hidden="true">
      <path d="M440 0 Q420 190 300 300 L525 300 L525 0 Z" fill="var(--brand-blue)"/>
      <path d="M420 0 Q400 185 282 300 L300 300 Q420 190 440 0 Z" fill="#fff"/>
      <path d="M398 0 Q380 180 262 300 L282 300 Q400 185 420 0 Z" fill="var(--brand-orange)"/>
    </svg>

    <div class="brand">
      <span class="brand-dot"></span>
      <span class="brand-name">Pinnel Garment Care</span>
    </div>

    <div class="contact">
      <p class="person-name">Jordan Mercer</p>
      <p class="address">18 Harbour Lane<br>Lota Qld 4179</p>
      <ul class="contact-list">
        <li>
          <svg class="contact-icon" viewBox="0 0 12 12"><rect x="2.5" y="0.5" width="7" height="11" rx="1.5" fill="none" stroke="var(--brand-orange)" stroke-width="1.2"/></svg>
          0412 508 736
        </li>
        <li>
          <svg class="contact-icon" viewBox="0 0 12 12"><path d="M3 1 L5 3.5 L4 5 Q5.5 7.5 7 8 L8.5 7 L11 9 L9.5 11 Q3 10 1 2.5 Z" fill="var(--brand-orange)"/></svg>
          (07) 3521 4806
        </li>
        <li>
          <svg class="contact-icon" viewBox="0 0 12 12"><rect x="0.5" y="2" width="11" height="8" fill="none" stroke="var(--brand-orange)" stroke-width="1.2"/><path d="M0.5 2 L6 6.5 L11.5 2" fill="none" stroke="var(--brand-orange)" stroke-width="1.2"/></svg>
          jordan@pinnelgarmentcare.com.au
        </li>
        <li>
          <svg class="contact-icon" viewBox="0 0 12 12"><circle cx="6" cy="6" r="5.3" fill="none" stroke="var(--brand-orange)" stroke-width="1.2"/><path d="M0.7 6 H11.3 M6 0.7 Q2.5 6 6 11.3 M6 0.7 Q9.5 6 6 11.3" fill="none" stroke="var(--brand-orange)" stroke-width="1"/></svg>
          www.pinnelgarmentcare.com.au
        </li>
      </ul>
    </div>
  </section>

  <section class="card card-back" aria-label="Business card back">
    <svg class="card-swoosh" viewBox="0 0 525 300" preserveAspectRatio="none" aria-hidden="true">
      <path d="M0 300 Q260 200 525 230 L525 300 Z" fill="var(--brand-blue)"/>
      <path d="M0 268 Q260 178 525 208 L525 230 Q260 200 0 300 Z" fill="#fff"/>
      <path d="M0 250 Q260 160 525 190 L525 208 Q260 178 0 268 Z" fill="var(--brand-orange)"/>
    </svg>
    <p class="locations">Northshore | Bayside | Harbour Pt</p>
  </section>

</main>
</body>
</html>
```